Vorn upkeep KT Solar Venture

Solar power system install
Services and maintenance
wiring, Rewinding and Renovation
Switch Board Upgrade
Power and lighting point
t doesn’t matter how much you spend on quality parts, your solar system will let you down if your design and installation are sub-par. Have your solar system tailored and installed by our Master Electrician and Bright Grid Guild Accredited team.

Target Market(s)

sales and installed

Industry/Entity Type

Solar install and retailer

Contact Information for Business Card

Name , Email, Phone Number ,Business address,

Font styles to use
Serif

Colors
0054AA
0677BA
7BADD7
CADEEF
E8F1F8

Requirements
Must have
• clear and bright
Nice to have
• new design
Should not have
• unclear pictures

```html
<!DOCTYPE html>
<html lang="en">
<head>
<meta charset="utf-8">
<title>Vorn upkeep · KT Solar Venture business card</title>
<link rel="stylesheet" href="https://fonts.googleapis.com/css2?family=Roboto:wght@400;500;700;900&display=swap">
<style>
  :root {
    --bg: #2b2b2b;
    --blue-deep: #0054aa;
    --blue: #0677ba;
    --blue-soft: #7badd7;
    --green: #6cb33f;
    --green-deep: #1f9a3c;
    --teal: #1e8a9c;
    --navy: #0c3f8e;
    --ink: #1c1c1c;
    --band: #e6e6e6;
    --paper: #f2f2f2;
    --white: #ffffff;
    --logo-disc: #f3b61f;
  }
  * { margin: 0; padding: 0; box-sizing: border-box; }
  html, body { width: 1200px; height: 1138px; overflow: hidden; }
  body {
    background: var(--bg);
    font-family: "Roboto", Arial, sans-serif;
    position: relative;
  }
  .card {
    position: absolute;
    border-radius: 16px;
    overflow: hidden;
  }
  /* Front */
  .card-front {
    left: 274px; top: 185px; width: 623px; height: 377px;
    background: linear-gradient(110deg, var(--blue) 0%, var(--teal) 45%, var(--green) 100%);
  }
  .brand {
    position: absolute;
    display: flex; align-items: center; gap: 18px;
  }
  .brand-dot {
    border-radius: 50%;
    background: var(--logo-disc);
    flex: none;
  }
  .brand-name {
    font-weight: 900;
    text-transform: uppercase;
    line-height: 1.08;
    letter-spacing: 0.5px;
  }
  .card-front .brand { left: 110px; top: 92px; }
  .card-front .brand-dot { width: 90px; height: 90px; }
  .card-front .brand-name { color: var(--white); font-size: 33px; }
  .services {
    position: absolute; left: 0; top: 240px; width: 100%; height: 73px;
    background: var(--band);
    display: flex; flex-direction: column; justify-content: center; align-items: center;
    color: var(--ink); font-size: 16.5px; line-height: 23px;
  }
  .site {
    position: absolute; left: 0; top: 333px; width: 100%;
    display: flex; justify-content: center; align-items: center; gap: 28px;
    color: var(--white); font-size: 15.5px;
  }
  .site .rule { width: 80px; height: 1.5px; background: rgba(255,255,255,.8); }

  /* Back */
  .card-back {
    left: 276px; top: 607px; width: 618px; height: 376px;
    background: var(--paper);
  }
  .card-back .brand { left: 22px; top: 50px; }
  .card-back .brand-dot { width: 96px; height: 96px; }
  .card-back .brand-name { color: var(--navy); font-size: 38px; }
  .person { position: absolute; left: 35px; top: 206px; }
  .person-name { color: #1660a8; font-size: 25px; font-weight: 500; }
  .person-title { color: var(--ink); font-size: 16px; margin-top: 4px; }
  .address { position: absolute; left: 35px; top: 292px; color: var(--ink); font-size: 16px; line-height: 24px; }
  .contacts { position: absolute; left: 345px; top: 232px; list-style: none; }
  .contacts li { display: flex; align-items: center; gap: 12px; height: 24px; font-size: 16.5px; color: var(--ink); }
  .contacts svg { width: 14px; height: 14px; fill: var(--green-deep); }
  .foot-green {
    position: absolute; left: 0; bottom: 0; width: 290px; height: 15px;
    background: linear-gradient(90deg, var(--green), var(--green-deep));
  }
  .foot-blue {
    position: absolute; right: 0; bottom: 0; width: 345px; height: 47px;
    background: linear-gradient(90deg, var(--blue), var(--blue-deep));
    clip-path: polygon(28px 0, 100% 0, 100% 100%, 0 100%);
    color: var(--white); font-size: 16.5px;
    padding-left: 63px; line-height: 42px;
  }
</style>
</head>
<body>
  <section class="card card-front">
    <div class="brand">
      <span class="brand-dot"></span>
      <div class="brand-name">Vorn upkeep<br>KT Solar Venture</div>
    </div>
    <div class="services">
      <p>Solar Power System Install &nbsp;|&nbsp; Wiring, Rewinding &amp; Renovation</p>
      <p>Services &amp; Maintenance &nbsp;|&nbsp; Switch Board Upgrade &nbsp;|&nbsp; Power &amp; Lighting Point</p>
    </div>
    <div class="site"><span class="rule"></span><span>www.ktsolarventure.com</span><span class="rule"></span></div>
  </section>

  <section class="card card-back">
    <div class="brand">
      <span class="brand-dot"></span>
      <div class="brand-name">Vorn upkeep<br>KT Solar Venture</div>
    </div>
    <div class="person">
      <p class="person-name">Ren Aldo Carter</p>
      <p class="person-title">Managing Director</p>
    </div>
    <p class="address">58 Harbor Lane, Elm City,<br>Elm Town, US 10245</p>
    <ul class="contacts">
      <li><svg viewBox="0 0 16 16" aria-hidden="true"><path d="M2 4c0-1 1-2 6-2s6 1 6 2v1.5h-3V4.5H5v1H2zM4 7h8l2 6H2z"/></svg>555-010-2040</li>
      <li><svg viewBox="0 0 16 16" aria-hidden="true"><path d="M1 3h14v10H1zM2.5 4.5v.4L8 9l5.5-4.1v-.4z" fill-rule="evenodd"/></svg>ren@ktsolarventure.com</li>
      <li><svg viewBox="0 0 16 16" aria-hidden="true"><path d="M8 1a7 7 0 1 0 0 14A7 7 0 0 0 8 1zm0 1.5c.8 0 1.7 1.6 2 4H6c.3-2.4 1.2-4 2-4zM3 7h1.9c0-.9.1-1.7.3-2.4A5.5 5.5 0 0 0 3 7zm8.1 0H13a5.5 5.5 0 0 0-2.2-2.4c.2.7.3 1.5.3 2.4zM6 8.5h4c-.2 2.6-1.1 5-2 5s-1.8-2.4-2-5zm-3 0a5.5 5.5 0 0 0 2.2 2.9c-.2-.8-.3-1.8-.4-2.9zm8 0c0 1.1-.1 2.1-.4 2.9A5.5 5.5 0 0 0 13 8.5z"/></svg>www.ktsolarventure.net</li>
    </ul>
    <div class="foot-green"></div>
    <div class="foot-blue">Solar power system install</div>
  </section>
</body>
</html>
```